Business Card Design & Gift cards, Gift Cert, Donation Card

Retail Gift Store-in addition to Business Cards we'd like sequenced 2 sided Gift cards, Gift Certificate Cards, and Donation Cards.please see examples and email for clarificationlogos attached with examples-
Gift Card, Gift Certificate and Donation Card will all be same style just differant upper right title, with back side info as example.
business card, as example is single sided.
looking for additional ideas for layout

Industry/Entity Type

Business

Contact Information for Business Card

211 Newman St.East Tawas, MI 48730989.362.8730Office@BrewKrew.com

Requirements
Must have
• Blue as per example
• Logos provided
• like gradiant background

```html
<!DOCTYPE html>
<html lang="en">
<head>
<meta charset="utf-8">
<title>Tillow Marsh — Business Card</title>
<link href="https://fonts.googleapis.com/css2?family=Alegreya+Sans+SC:wght@400&display=swap" rel="stylesheet">
<style>
  :root {
    --page: #ecebe8;
    --edge-yellow: #e6dc1c;
    --frame-blue: #4566b8;
    --frame-blue-light: #5a7bc8;
    --card-white: #ffffff;
    --card-white-soft: #eef0f4;
    --ink-blue: #4a68b8;
    --ink-dark: #2b2f3a;
    --icon-bg: #5273c0;
  }
  * { box-sizing: border-box; margin: 0; padding: 0; }
  html, body {
    width: 1200px;
    height: 892px;
    overflow: hidden;
    background: var(--page);
  }
  .sheet {
    position: relative;
    width: 1200px;
    height: 892px;
    display: flex;
    align-items: center;
    justify-content: center;
    gap: 40px;
  }
  .card {
    width: 540px;
    height: 310px;
    border: 4px solid var(--edge-yellow);
    background: linear-gradient(135deg, var(--frame-blue-light), var(--frame-blue));
    padding: 30px 34px;
    box-shadow: 0 6px 18px rgba(0,0,0,0.18);
  }
  .card-face {
    position: relative;
    width: 100%;
    height: 100%;
    background: linear-gradient(160deg, var(--card-white) 40%, var(--card-white-soft));
    font-family: "Alegreya Sans SC", "Trebuchet MS", sans-serif;
  }
  .brand {
    display: flex;
    align-items: center;
    gap: 10px;
    color: var(--ink-blue);
    font-size: 30px;
    letter-spacing: 1px;
    white-space: nowrap;
  }
  .brand-dot {
    width: 34px;
    height: 34px;
    border-radius: 50%;
    background: var(--edge-yellow);
    flex: none;
  }
  .card--front .brand {
    position: absolute;
    left: 24px;
    bottom: 36px;
  }
  .contact-list {
    position: absolute;
    left: 250px;
    top: 46px;
    list-style: none;
    color: var(--ink-dark);
    font-size: 17px;
    line-height: 1.3;
  }
  .contact-item {
    display: flex;
    align-items: flex-start;
    gap: 8px;
    margin-bottom: 6px;
  }
  .contact-icon {
    width: 16px;
    height: 16px;
    flex: none;
    margin-top: 3px;
    background: var(--icon-bg);
    border-radius: 2px;
  }
  .card--back .brand {
    position: absolute;
    left: 50%;
    top: 50%;
    transform: translate(-50%, -50%);
    font-size: 34px;
  }
</style>
</head>
<body>
<main class="sheet">
  <section class="card card--front" aria-label="Business card front">
    <div class="card-face">
      <div class="brand"><span class="brand-dot"></span><span class="brand-name">Tillow Marsh</span></div>
      <ul class="contact-list">
        <li class="contact-item">
          <svg class="contact-icon" viewBox="0 0 16 16" aria-hidden="true"><rect width="16" height="16" rx="2" fill="#5273c0"/><path d="M5 3.5h2l.8 2.4-1.2.9a6 6 0 0 0 2.6 2.6l.9-1.2 2.4.8v2A1.2 1.2 0 0 1 11.3 12.5 8 8 0 0 1 3.5 4.7 1.2 1.2 0 0 1 5 3.5z" fill="#fff"/></svg>
          <span>989.517.4296</span>
        </li>
        <li class="contact-item">
          <svg class="contact-icon" viewBox="0 0 16 16" aria-hidden="true"><rect width="16" height="16" rx="2" fill="#5273c0"/><rect x="3" y="4.5" width="10" height="7" fill="none" stroke="#fff" stroke-width="1.2"/><path d="M3 4.5l5 4 5-4" fill="none" stroke="#fff" stroke-width="1.2"/></svg>
          <span>Office@TillowMarsh.com</span>
        </li>
        <li class="contact-item">
          <svg class="contact-icon" viewBox="0 0 16 16" aria-hidden="true"><rect width="16" height="16" rx="2" fill="#5273c0"/><path d="M8 13s-3.5-4-3.5-6.5a3.5 3.5 0 0 1 7 0C11.5 9 8 13 8 13z" fill="#fff"/><circle cx="8" cy="6.5" r="1.3" fill="#5273c0"/></svg>
          <span>482 Larkfield Ave. Harlow Bay,<br>MI 48915</span>
        </li>
      </ul>
    </div>
  </section>

  <section class="card card--back" aria-label="Business card back">
    <div class="card-face">
      <div class="brand"><span class="brand-dot"></span><span class="brand-name">Tillow Marsh</span></div>
    </div>
  </section>
</main>
</body>
</html>
```